Cove medical spa and wellness

Integrate existing logo and web design (colors and background) into tri fold, single card brochure and business card design. We already have a logo and an idea for our promotional material but we would like someone to bring it together for us! Covewellnessandspa.com. We want to see what a marble background with a faded lily (as seen on our webpage) would look like on brochures and business cards.

```html
<!DOCTYPE html>
<html lang="en">
<head>
<meta charset="utf-8">
<title>Cove Medical Spa &amp; Wellness — Business Card</title>
<link href="https://fonts.googleapis.com/css2?family=Poppins:wght@400&family=Dancing+Script:wght@700&display=swap" rel="stylesheet">
<style>
  :root {
    --page: #2b2b2d;
    --card-white: #f7f7f5;
    --gold-dark: #a6782a;
    --gold-mid: #c79b3b;
    --gold-light: #dcc266;
    --ink-white: #ffffff;
    --back-black: #1f1f21;
    --back-grey: #8a8a8c;
  }
  * { margin: 0; padding: 0; box-sizing: border-box; }
  html, body { width: 1200px; height: 960px; overflow: hidden; background: var(--page); }
  .canvas {
    width: 1200px; height: 960px;
    display: flex; flex-direction: column; align-items: center; justify-content: center; gap: 40px;
  }
  .card {
    position: relative; width: 700px; height: 400px; overflow: hidden;
    box-shadow: 0 10px 30px rgba(0,0,0,.45);
  }
  /* Back */
  .card-back {
    background: radial-gradient(ellipse at 50% 50%, #2a2a2c 0%, var(--back-black) 75%);
    display: flex; align-items: center; justify-content: center; gap: 16px;
  }
  .card-back .mark-dot { width: 22px; height: 22px; border-radius: 50%; background: var(--back-grey); }
  .card-back .brand {
    font-family: "Poppins", sans-serif; font-weight: 400; font-size: 54px;
    color: var(--back-grey); letter-spacing: 2px;
  }
  /* Front */
  .card-front { background: var(--card-white); }
  .card-front .wave { position: absolute; inset: 0; }
  .brand-block {
    position: absolute; left: 60px; top: 110px; display: flex; align-items: center; gap: 12px;
  }
  .brand-block .mark-dot { width: 16px; height: 16px; border-radius: 50%; background: var(--gold-mid); }
  .brand-block .brand {
    font-family: "Poppins", sans-serif; font-weight: 400; font-size: 22px;
    color: var(--gold-mid); line-height: 1.2;
  }
  .contact {
    position: absolute; right: 36px; top: 66px; text-align: right; color: var(--ink-white);
    font-family: "Poppins", sans-serif; font-weight: 400;
  }
  .contact .person {
    font-family: "Dancing Script", cursive; font-weight: 700; font-size: 32px; margin-bottom: 6px;
  }
  .contact .address { font-size: 13px; line-height: 1.35; margin-bottom: 10px; }
  .contact .line { font-size: 14px; line-height: 1.5; display: flex; justify-content: flex-end; align-items: center; gap: 6px; }
  .contact svg { width: 12px; height: 12px; fill: var(--ink-white); flex: none; }
</style>
</head>
<body>
<main class="canvas">
  <section class="card card-back" aria-label="Card back">
    <span class="mark-dot"></span>
    <span class="brand">Cove</span>
  </section>

  <section class="card card-front" aria-label="Card front">
    <svg class="wave" viewBox="0 0 700 400" preserveAspectRatio="none" aria-hidden="true">
      <defs>
        <linearGradient id="goldFill" x1="0" y1="1" x2="1" y2="0">
          <stop offset="0" stop-color="#a6782a"/>
          <stop offset="0.55" stop-color="#dcc266"/>
          <stop offset="1" stop-color="#a6782a"/>
        </linearGradient>
      </defs>
      <path d="M700,14 C500,4 450,70 390,175 C330,285 260,322 0,326 L0,400 L700,400 Z" fill="url(#goldFill)"/>
      <path d="M690,20 C495,14 440,82 376,186 C318,286 250,312 60,312" fill="none" stroke="#c79b3b" stroke-width="1.5"/>
    </svg>

    <div class="brand-block">
      <span class="mark-dot"></span>
      <span class="brand">Cove medical spa<br>and wellness</span>
    </div>

    <div class="contact">
      <div class="person">Daniel Morgan</div>
      <div class="address">4820 N. Palm Avenue, Suite 12<br>Mesa, AZ 85201</div>
      <div class="line">(480) 555-0142
        <svg viewBox="0 0 24 24"><path d="M6.6 10.8a15 15 0 0 0 6.6 6.6l2.2-2.2a1 1 0 0 1 1-.25 11.4 11.4 0 0 0 3.6.57 1 1 0 0 1 1 1V20a1 1 0 0 1-1 1A17 17 0 0 1 3 4a1 1 0 0 1 1-1h3.5a1 1 0 0 1 1 1c0 1.25.2 2.45.57 3.57a1 1 0 0 1-.25 1z"/></svg>
      </div>
      <div class="line">welcome@covewellnessandspa.com
        <svg viewBox="0 0 24 24"><path d="M2 5h20v14H2z M3.5 6.5 12 13l8.5-6.5" /></svg>
      </div>
      <div class="line">www.covewellnessandspa.com
        <svg viewBox="0 0 24 24"><circle cx="12" cy="12" r="10"/></svg>
      </div>
    </div>
  </section>
</main>
</body>
</html>
```